Landscape design build company door flyer

I would like this flyer to convey a high-level of professionalism for a company that is excellent with communication with their clients as well as a company that does incredible installations

Went on vacation/holiday

```html
<!DOCTYPE html>
<html lang="en">
<head>
<meta charset="utf-8">
<title>Summit Ridge Builders – Outdoor Living Flyer</title>
<link rel="stylesheet" href="https://fonts.googleapis.com/css2?family=Montserrat:wght@400;500;600;700;800;900&display=swap">
<style>
  :root{
    --navy:#0f2d44;
    --navy-band:#12293b;
    --orange:#f36f12;
    --white:#ffffff;
    --ink:#1d1d1d;
    --backdrop:#9a9a9a;
  }
  *{margin:0;padding:0;box-sizing:border-box}
  html,body{width:1200px;height:933px;overflow:hidden}
  body{background:var(--backdrop);font-family:'Montserrat',sans-serif;position:relative}

  .flyer{position:absolute;left:253px;top:20px;width:694px;height:893px;background:var(--white);overflow:hidden}
  .abs{position:absolute}

  .hero-photo{left:0;top:218px;width:694px;height:234px;
    background:linear-gradient(180deg,#3f4a3a 0%,#8a4a26 35%,#b8582a 60%,#6b4632 80%,#6c9a3a 100%)}
  .header-band{left:0;top:0;width:694px;height:260px}

  .brand{left:14px;top:92px;width:210px;text-align:center;color:var(--orange)}
  .brand-mark{width:44px;height:44px;border-radius:50%;background:var(--orange);margin:0 auto 10px}
  .brand-name{font-weight:600;font-size:16px;letter-spacing:.3px}
  .brand-tag{font-size:8px;font-weight:500;color:var(--navy);margin-top:2px;letter-spacing:.4px}

  .headline-top{left:292px;top:46px;font-weight:800;font-size:45px;color:var(--navy);letter-spacing:1px;line-height:1}
  .headline-main{left:290px;top:90px;font-weight:900;font-size:86px;color:var(--orange);line-height:1;letter-spacing:1px}
  .band-text{left:292px;top:188px;font-weight:800;font-size:25px;color:var(--white);line-height:28px;letter-spacing:.2px}

  .photo-frame{left:29px;top:397px;width:266px;height:362px;background:var(--white)}
  .gallery-photo{left:33px;width:257px}
  .gallery-photo.garden{top:402px;height:104px;background:linear-gradient(160deg,#4d5a3c,#8d8f86 45%,#b7bcbd 70%,#5f7a3a)}
  .gallery-photo.deck{top:523px;height:105px;background:linear-gradient(150deg,#b88a5e,#8e7a67 45%,#9ea3a6 75%,#6f7d55)}
  .gallery-photo.platform{top:645px;height:104px;background:linear-gradient(180deg,#8d8f90 0%,#9b7a5a 35%,#7f5d40 65%,#b6a78f 100%)}

  .section-title{left:318px;font-weight:800;font-size:18px;color:var(--navy);letter-spacing:.2px}
  .section-rule{left:318px;width:334px;height:2px;background:var(--ink)}
  .section-rule::before{content:"";position:absolute;left:0;top:1px;width:82px;height:3px;background:var(--orange)}
  .about-title{top:470px}
  .about-rule{top:496px}
  .services-title{top:648px}
  .services-rule{top:675px}

  .about-copy{left:318px;top:503px;width:334px;font-size:11.8px;line-height:14.6px;color:var(--ink);text-align:justify}

  .services{left:318px;top:689px;width:360px;display:grid;grid-template-columns:181px 179px;row-gap:6.5px;list-style:none}
  .services li{display:flex;align-items:center;gap:10px;font-size:13px;font-weight:500;color:var(--ink);height:15px;letter-spacing:.2px}
  .services svg{width:11px;height:11px;flex:none}

  .cta-band{left:0;top:778px;width:694px;height:56px;background:var(--navy-band);display:flex;align-items:center;justify-content:center}
  .cta-band span{color:var(--white);font-weight:800;font-size:24.5px;letter-spacing:.4px}

  .contact-row{left:0;top:843px;width:694px;height:24px;display:flex;align-items:center;justify-content:center;color:var(--navy);font-weight:700}
  .contact-item{display:flex;align-items:center;gap:6px;white-space:nowrap}
  .contact-item svg{width:12px;height:12px;flex:none}
  .phone{font-size:16.5px}
  .email,.web{font-size:11px;letter-spacing:.2px}
  .divider{width:2px;height:18px;background:var(--ink);margin:0 10px}
</style>
</head>
<body>
  <main class="flyer">
    <div class="abs hero-photo" role="img" aria-label="Photo of a wooden cabin with a wraparound porch and cross-braced railings in a wooded yard"></div>

    <svg class="abs header-band" viewBox="0 0 694 260" aria-hidden="true">
      <polygon points="0,0 694,0 694,174 215,174 154,218 0,218" fill="var(--white)"/>
      <polygon points="215,174 694,174 694,251 154,251" fill="var(--orange)"/>
      <polyline points="154,0 269,125 215,174" fill="none" stroke="#111" stroke-width="8"/>
    </svg>

    <div class="abs brand">
      <div class="brand-mark"></div>
      <div class="brand-name">SUMMIT RIDGE BUILDERS</div>
      <div class="brand-tag">OUTDOOR LIVING SPACES</div>
    </div>

    <h1 class="abs headline-top">LOVE COMING</h1>
    <div class="abs headline-main">HOME?</div>
    <p class="abs band-text">LET US REIMAGINE YOUR<br>OUTDOOR LIVING AREA</p>

    <div class="abs photo-frame"></div>
    <div class="abs gallery-photo garden" role="img" aria-label="Photo of a paver patio with curved stone steps and a planted garden slope"></div>
    <div class="abs gallery-photo deck" role="img" aria-label="Photo of a two-level wooden deck with stairs and railings"></div>
    <div class="abs gallery-photo platform" role="img" aria-label="Photo of a low composite deck platform with wide steps"></div>

    <h2 class="abs section-title about-title">ABOUT US</h2>
    <div class="abs section-rule about-rule"></div>
    <p class="abs about-copy">Discover the endless possibilities for your outdoor space with The Summit Ridge Team. Our team of skilled artisans is dedicated to turning your outdoor space into a breathtaking oasis that you’ll love coming home to. Whether it’s a cozy patio for intimate gatherings, a sprawling deck to host memorable parties, or a custom paver driveway that adds instant curb appeal, our high-quality craftsmanship ensures stunning results that exceed your expectations.</p>

    <h2 class="abs section-title services-title">OUR SERVICES</h2>
    <div class="abs section-rule services-rule"></div>
    <ul class="abs services">
      <li><svg viewBox="0 0 12 12"><circle cx="6" cy="6" r="6" fill="var(--orange)"/><path d="M3.2 6.2l1.9 1.9 3.7-3.9" stroke="#fff" stroke-width="1.6" fill="none"/></svg>PAVER PATIOS</li>
      <li><svg viewBox="0 0 12 12"><circle cx="6" cy="6" r="6" fill="var(--orange)"/><path d="M3.2 6.2l1.9 1.9 3.7-3.9" stroke="#fff" stroke-width="1.6" fill="none"/></svg>POOLS</li>
      <li><svg viewBox="0 0 12 12"><circle cx="6" cy="6" r="6" fill="var(--orange)"/><path d="M3.2 6.2l1.9 1.9 3.7-3.9" stroke="#fff" stroke-width="1.6" fill="none"/></svg>PAVER DRIVEWAYS</li>
      <li><svg viewBox="0 0 12 12"><circle cx="6" cy="6" r="6" fill="var(--orange)"/><path d="M3.2 6.2l1.9 1.9 3.7-3.9" stroke="#fff" stroke-width="1.6" fill="none"/></svg>OUTDOOR LIGHTING</li>
      <li><svg viewBox="0 0 12 12"><circle cx="6" cy="6" r="6" fill="var(--orange)"/><path d="M3.2 6.2l1.9 1.9 3.7-3.9" stroke="#fff" stroke-width="1.6" fill="none"/></svg>RETAINING WALLS</li>
      <li><svg viewBox="0 0 12 12"><circle cx="6" cy="6" r="6" fill="var(--orange)"/><path d="M3.2 6.2l1.9 1.9 3.7-3.9" stroke="#fff" stroke-width="1.6" fill="none"/></svg>FIREPITS &amp; FIREPLACES</li>
      <li><svg viewBox="0 0 12 12"><circle cx="6" cy="6" r="6" fill="var(--orange)"/><path d="M3.2 6.2l1.9 1.9 3.7-3.9" stroke="#fff" stroke-width="1.6" fill="none"/></svg>DECKS &amp; RAILINGS</li>
      <li><svg viewBox="0 0 12 12"><circle cx="6" cy="6" r="6" fill="var(--orange)"/><path d="M3.2 6.2l1.9 1.9 3.7-3.9" stroke="#fff" stroke-width="1.6" fill="none"/></svg>AND MORE...</li>
    </ul>

    <div class="abs cta-band"><span>CONTACT US TODAY FOR A FREE ESTIMATE</span></div>

    <div class="abs contact-row">
      <div class="contact-item phone">
        <svg viewBox="0 0 12 12"><path d="M2.3 0.8l2 2-1 1.4c.7 1.6 2 2.9 3.6 3.6l1.4-1 2 2-1.3 2.2C4.9 10.6 1.4 7.1.9 2.1z" fill="var(--orange)"/></svg>
        206-555-0148
      </div>
      <span class="divider"></span>
      <div class="contact-item email">
        <svg viewBox="0 0 12 12"><rect x="0.5" y="2" width="11" height="8" fill="var(--orange)"/><path d="M0.8 2.4L6 6.6l5.2-4.2" stroke="#fff" stroke-width="1.1" fill="none"/></svg>
        INFO@SUMMITRIDGEBUILDERS.COM
      </div>
      <span class="divider"></span>
      <div class="contact-item web">
        <svg viewBox="0 0 12 12" fill="none" stroke="var(--orange)" stroke-width="1"><circle cx="6" cy="6" r="5.2"/><ellipse cx="6" cy="6" rx="2.3" ry="5.2"/><path d="M0.8 6h10.4M1.6 3.4h8.8M1.6 8.6h8.8"/></svg>
        WWW.SUMMITRIDGEBUILDERS.COM
      </div>
    </div>
  </main>
</body>
</html>
```